Sophisticated, clean website reflecting my feminine, playful side to sell my abstract art,

I need a website no more than 3 pages to showcase my paintings, a little about me and some contact info. I do abstracts so looking for something a little edgy, yet feminine and current.
Updates

Hi there, These are some artists websites that I Iike: Marnelvoss.com (I like how airy it is) peterwallombry.com garethpolvens.com (I like how it scrolls) I'll need a place for a photo ( a headshot-i do not have it yet so I'll need to be able to upload that later) as well as an area for my bio. Also, it's important that I will be able to upload any new photos and descriptions easily so it should be user friendly. Lastly, I like in a sunny place so would like to have this seem upbeat and playful as that is how i like to paint. thanks-I'm trying to upload my photos now -

Target Market(s)

ppl ages 35-70 who want large scale art for their homes

Industry/Entity Type

art

Coding

Coded - Design and coding required

Number of Pages Required

3 page

Colors

Designer to choose colors to be used in the design.

Requirements
Must have
• photos of my art, a place for my bio, be easy to reach me. tasteful-nothing too "in your face" -my clients are pretty high end and organized. They like clean lines
Nice to have
• sophisticated background, muted tones in the back-similar clean font throughout-no cursive
Should not have
• too many dark areas. Too many blocks of color. Too serious.

```html
<!DOCTYPE html>
<html lang="en">
<head>
<meta charset="utf-8">
<title>Helena Marsh — Abstract Art</title>
<link rel="stylesheet" href="https://fonts.googleapis.com/css2?family=EB+Garamond:wght@400;500&family=Roboto:wght@700;900&family=Poppins:wght@400&display=swap">
<style>
:root{
  --ink:#111111;
  --paper:#ffffff;
  --accent:#c0735f;
  --field:#e8e8e8;
  --muted:#8a8a8a;
  --avatar:#d9c7a8;
  --hero-a:#e6dfe8;
  --hero-b:#4fa64a;
  --hero-c:#1f7a73;
  --hero-d:#c5e07a;
}
*{margin:0;padding:0;box-sizing:border-box}
html,body{width:1200px;height:3187px;overflow:hidden;background:var(--paper)}
body{position:relative;font-family:"EB Garamond",Georgia,serif;color:var(--ink)}
.abs{position:absolute}

/* Header */
.site-header{position:absolute;left:0;top:0;width:1200px;height:169px;background:var(--paper);box-shadow:0 10px 22px rgba(0,0,0,.12);z-index:2}
.brand-rule{position:absolute;top:53px;height:3px;background:var(--ink)}
.brand-rule.left{left:25px;width:204px}
.brand-rule.right{left:959px;width:200px}
.brand-name{position:absolute;left:229px;width:730px;top:22px;text-align:center;font-family:"Roboto",Arial,sans-serif;font-weight:900;font-size:50px;letter-spacing:20px;line-height:60px;padding-left:20px;white-space:nowrap}
.brand-mark{position:absolute;left:560px;top:100px;width:80px;text-align:center;font-family:"Roboto",Arial,sans-serif;font-weight:700;font-size:34px;line-height:40px}
.main-nav a{position:absolute;top:110px;font-size:20px;color:var(--ink);text-decoration:none;text-shadow:0 1px 1px rgba(0,0,0,.25)}

/* Hero */
.hero{position:absolute;left:0;top:169px;width:1200px;height:578px;
  background:
    radial-gradient(ellipse at 30% 40%,var(--hero-b) 0%,transparent 45%),
    radial-gradient(ellipse at 70% 60%,var(--hero-d) 0%,transparent 40%),
    radial-gradient(ellipse at 55% 25%,var(--hero-c) 0%,transparent 30%),
    linear-gradient(120deg,var(--hero-a),#9bc98c 50%,var(--hero-a));
  box-shadow:0 14px 26px rgba(0,0,0,.12)}
.slider-dots{position:absolute;left:513px;top:701px;display:flex;gap:7.5px}
.slider-dots span{width:15px;height:15px;border-radius:50%;background:var(--paper)}
.slider-dots span.active{background:transparent;border:2px solid var(--paper)}

/* Bio */
.portrait{position:absolute;left:183px;top:862px;width:282px;height:288px;background:linear-gradient(180deg,var(--avatar),#cfcfcf);border-radius:140px 140px 12px 12px}
.eyebrow{position:absolute;color:var(--accent);font-size:22px;letter-spacing:.5px}
.section-title{position:absolute;font-weight:400;letter-spacing:1px}
.bio-handle{left:623px;top:877px;font-size:32px}
.bio-icon{position:absolute;left:893px;top:885px;width:26px;height:26px;border:3px solid var(--ink);border-radius:50%}
.copy{position:absolute;font-size:16.7px;line-height:19.2px}
.copy p+p{margin-top:19px}

/* Gallery */
.gallery-title{position:absolute;left:0;width:1200px;top:1280px;text-align:center;font-size:35px;letter-spacing:.5px}
.artwork{position:absolute;border:3px solid var(--ink)}
.caption{position:absolute;width:240px;text-align:center;font-size:19px}
.btn{position:absolute;background:var(--ink);color:var(--paper);text-align:center;font-size:16px;letter-spacing:.5px}

/* Contact */
.enquiry-card{position:absolute;left:130px;top:2654px;width:336px;height:371px;background:var(--paper);box-shadow:0 0 60px rgba(0,0,0,.14)}
.enquiry-card h3{position:absolute;left:30px;top:34px;font-weight:400;font-size:19px;line-height:20px;letter-spacing:.4px}
.field{position:absolute;left:30px;width:277px;background:var(--field);font-size:9px;color:var(--muted);padding:5px 15px}

.site-footer{position:absolute;left:0;top:3111px;width:1200px;height:76px;background:var(--ink);color:var(--paper);font-family:"Poppins",Arial,sans-serif;font-size:15px;text-align:center;line-height:76px}
</style>
</head>
<body>

<header class="site-header">
  <div class="brand-rule left"></div>
  <div class="brand-name">HELENA MARSH</div>
  <div class="brand-rule right"></div>
  <div class="brand-mark">HM</div>
  <nav class="main-nav">
    <a href="#about" style="left:755px">About me</a>
    <a href="#gallery" style="left:909px">Gallery</a>
    <a href="#contact" style="left:1044px">Contact us</a>
  </nav>
</header>

<section class="hero" role="img" aria-label="Close-up of a green, teal and lilac abstract painting"></section>
<div class="slider-dots" style="z-index:3"><span class="active"></span><span></span><span></span><span></span><span></span><span></span><span></span><span></span></div>

<section id="about">
  <div class="portrait" role="img" aria-label="Placeholder for the artist's headshot"></div>
  <div class="eyebrow" style="left:631px;top:852px">Bio Graphy</div>
  <h2 class="section-title bio-handle">HMARSHART</h2>
  <span class="bio-icon"></span>
  <div class="copy" style="left:619px;top:936px;width:430px">
    <p>Lorem ipsum dolor sit amet, consectetur estor adipi isicing elit, sed do eiusmod tempor este uterre incididui unt ut labore et dolore magna aliquaas. Ut enim ad minim veniam, quis mot nostrud desto exercitation est ullamco laboris nisi ut se aliquip ex ea commodos consequat.</p>
    <p>Duis aute irure et dolor in reprehender itinse voluptate velit esse cillum dolore eu fugiat do nulla pariatur deus ex. Excepteur sint occaecat er cupidatat non ullamco proident, sunt in dos Lorem ipsum dolor sit amet, consectetur adipisic eli sed do eiusmod tempor incididunt ut labore et dolore si magna</p>
  </div>
</section>

<section id="gallery">
  <h2 class="gallery-title section-title">Gallery</h2>
  <div class="artwork" style="left:156px;top:1371px;width:240px;height:246px;background:linear-gradient(135deg,#ece6e2,#5a2520 55%,#d8c7c2)" role="img" aria-label="Abstract painting in burgundy and white"></div>
  <div class="artwork" style="left:470px;top:1371px;width:240px;height:246px;background:radial-gradient(circle,#7a3a30,#e7b9bf 60%,#f0e0dc)" role="img" aria-label="Abstract rose painting in pink and brown"></div>
  <div class="artwork" style="left:786px;top:1371px;width:240px;height:246px;background:linear-gradient(90deg,#1a8a86 0 10%,#ddd8cc 10% 60%,#1f3c8a 75%)" role="img" aria-label="Abstract painting in teal, cream and blue"></div>
  <div class="caption" style="left:156px;top:1630px">Buy Now</div>
  <div class="caption" style="left:470px;top:1630px">Buy Now</div>
  <div class="caption" style="left:786px;top:1630px">Buy Now</div>

  <div class="artwork" style="left:150px;top:1697px;width:249px;height:254px;background:radial-gradient(circle,#1d3a5a,#d49a20 45%,#efe6d2)" role="img" aria-label="Abstract painting in ochre, navy and white"></div>
  <div class="artwork" style="left:468px;top:1701px;width:240px;height:246px;background:radial-gradient(circle,#3b2f8a,#9a7ab8 45%,#ece6e4)" role="img" aria-label="Abstract painting in violet and cream"></div>
  <div class="artwork" style="left:784px;top:1701px;width:240px;height:246px;background:radial-gradient(circle,#8a2e18,#c86a48 45%,#efe2da)" role="img" aria-label="Abstract rose painting in rust red"></div>
  <div class="caption" style="left:154px;top:1960px">Buy Now</div>
  <div class="caption" style="left:468px;top:1960px">Buy Now</div>
  <div class="caption" style="left:784px;top:1960px">Buy Now</div>

  <a class="btn" style="left:536px;top:2040px;width:130px;height:37px;line-height:37px">Explore More</a>
</section>

<section id="works">
  <div class="eyebrow" style="left:106px;top:2190px">The Museum archive</div>
  <h2 class="section-title" style="left:106px;top:2223px;font-size:37px">WORKS OF ART</h2>
  <div class="copy" style="left:106px;top:2278px;width:490px">
    <p>Lorem ipsum dolor sit amet, consectetur estor adipi isicing elit, sed do eiusmod tempor este uterre incididui unt ut labore et dolore magna aliquaas. Ut enim ad minim veniam, quis mot nostrud desto exercitation est ullamco laboris nisi ut se aliquip ex ea commodos consequat.</p>
    <p>Duis aute irure et dolor in reprehender itinse voluptate velit esse cillum dolore eu fugiat do nulla pariatur deus ex. Excepteur sint occaecat er cupidatat non ullamco proident, sunt in dos<br>Lorem ipsum dolor sit amet, consectetur adipisic eli sed do eiusmod tempor incididunt ut labore et dolore si magna aliqua. Ut enim adese</p>
  </div>
  <a class="btn" style="left:106px;top:2503px;width:129px;height:35px;line-height:35px">Contact us</a>
  <div class="abs" style="left:668px;top:2177px;width:433px;height:368px;background:radial-gradient(circle at 30% 65%,#6a3a3a,#e2a9b0 40%,#f0d8cc 60%,#4a2a3a 95%)" role="img" aria-label="Large abstract floral painting in pink, peach and plum"></div>
</section>

<section id="contact">
  <form class="enquiry-card">
    <h3>Fill the form if you want to get<br>more information about painting</h3>
    <div class="field" style="top:93px;height:23px">Enter Your Name</div>
    <div class="field" style="top:127px;height:22px">Enter Your Email</div>
    <div class="field" style="top:160px;height:24px">Enter Your Number</div>
    <div class="field" style="top:195px;height:92px">write massage</div>
    <div class="btn" style="left:30px;top:300px;width:68px;height:31px;line-height:31px;font-size:17px">Send</div>
  </form>
  <h2 class="section-title" style="left:593px;top:2692px;font-size:35px">Get in Touch</h2>
  <div class="copy" style="left:597px;top:2755px;width:500px">
    <p>Lorem ipsum dolor sit amet, consectetur estor adipi isicing elit, sed do eiusmod tempor este uterre incididui unt ut labore et dolore magna aliquaas. Ut enim ad minim veniam, quis mot nostrud desto exercitation est ullamco laboris nisi ut se aliquip ex ea commodos consequat.</p>
    <p>Duis aute irure et dolor in reprehender itinse voluptate velit esse cillum dolore eu fugiat do nulla pariatur deus ex. Excepteur sint occaecat er cupidatat non ullamco proident, sunt in dos Lorem ipsum dolor sit amet, consectetur adipisic eli sed do eiusmod tempor incididunt ut labore et dolore si magna aliqua. Ut enim adese</p>
  </div>
</section>

<footer class="site-footer">Copyright hmarshart 2021 All Rights Reserved</footer>

</body>
</html>
```